Business card design needed

I would like a one sided black business card with the information provided above. Refer to my website www.brightvolleyracquets.com.au for an example of colors I have used for my site, would like to keep this consistent for my business cards also, I will upload my logo below.

I am a new small business that provides tennis customers with racquet re stringing, tennis strings and accessories.

Industry/Entity Type

Small Business

Contact Information for Business Card

Bright Volley Tennis

Owen Whitby
Managing Director

brightvolleyracquets@mailbox.example
www.brightvolleyracquets.com.au
0491 726 305

Racquet Restringing/Tennis Strings/Accessories

Requirements
Must have
• Must have my logo and card must be black

```html
<!DOCTYPE html>
<html lang="en">
<head>
<meta charset="utf-8">
<title>Bright Volley Tennis — Business Card</title>
<link rel="stylesheet" href="https://fonts.googleapis.com/css2?family=Source+Sans+3:ital,wght@0,400;0,600;0,700;1,700&display=swap">
<style>
  :root {
    --page: #e9e6e1;
    --card-black: #030404;
    --lime: #b9d43a;
    --blue: #24508a;
    --white: #ffffff;
    --ink: #0a0a0a;
  }
  html, body {
    margin: 0;
    width: 1200px;
    height: 750px;
    overflow: hidden;
    background: var(--page);
    font-family: "Source Sans 3", "Myriad Pro", Arial, sans-serif;
  }
  .card {
    position: absolute;
    left: 75px;
    top: 75px;
    width: 1050px;
    height: 600px;
    border-radius: 36px;
    background: var(--card-black);
    overflow: hidden;
    box-shadow: 0 4px 14px rgba(0,0,0,0.25);
  }
  .card-waves {
    position: absolute;
    inset: 0;
  }
  .brand {
    position: absolute;
    left: 50px;
    top: 180px;
    width: 600px;
    display: flex;
    align-items: center;
    justify-content: center;
    gap: 18px;
    color: var(--lime);
    font-weight: 700;
    font-size: 62px;
    letter-spacing: 0.5px;
    line-height: 1;
  }
  .brand-dot {
    width: 52px;
    height: 52px;
    border-radius: 50%;
    background: var(--lime);
    flex: none;
  }
  .divider {
    position: absolute;
    left: 694px;
    top: 162px;
    width: 2px;
    height: 131px;
    background: var(--white);
  }
  .contact {
    position: absolute;
    left: 733px;
    top: 156px;
    color: var(--white);
  }
  .contact-name {
    margin: 0;
    color: var(--lime);
    font-weight: 700;
    font-size: 33px;
    line-height: 1.1;
  }
  .contact-role {
    margin: 2px 0 0;
    font-size: 26px;
    line-height: 1.2;
  }
  .contact-phone {
    margin: 34px 0 0;
    font-size: 26px;
    line-height: 1.2;
  }
  .label {
    font-weight: 700;
    font-style: italic;
  }
  .services {
    position: absolute;
    left: 44px;
    top: 346px;
    margin: 0;
    padding: 0;
    list-style: none;
    display: flex;
    gap: 10px;
    color: var(--white);
    font-size: 26px;
  }
  .services li::before {
    content: "";
    display: inline-block;
    width: 8px;
    height: 8px;
    background: var(--white);
    margin-right: 9px;
    vertical-align: 5px;
  }
  .web-line {
    position: absolute;
    left: 0;
    right: 0;
    top: 538px;
    margin: 0;
    text-align: center;
    color: var(--ink);
    font-size: 25px;
  }
</style>
</head>
<body>
  <main class="card">
    <svg class="card-waves" viewBox="0 0 1050 600" aria-hidden="true">
      <path fill="var(--blue)" d="M690,498 C850,488 990,410 1050,316 L1050,388 C980,450 850,496 690,498 Z"/>
      <path fill="#000" d="M690,498 C850,496 980,452 1050,388 L1050,402 C985,455 850,500 690,498 Z"/>
      <path fill="var(--lime)" d="M0,540 C40,495 150,470 300,478 C450,488 560,500 690,498 C850,496 990,445 1050,400 L1050,600 L0,600 Z"/>
    </svg>

    <div class="brand">
      <span class="brand-dot"></span>
      <span class="brand-name">Bright Volley Tennis</span>
    </div>

    <div class="divider"></div>

    <div class="contact">
      <p class="contact-name">Owen Whitby</p>
      <p class="contact-role">Managing Director</p>
      <p class="contact-phone"><span class="label">phone</span> 0491 726 305</p>
    </div>

    <ul class="services">
      <li>Racquet Restringing</li>
      <li>Tennis Strings</li>
      <li>Accessories</li>
    </ul>

    <p class="web-line"><span class="label">email</span> brightvolleyracquets@mailbox.example | <span class="label">web</span> www.brightvolleyracquets.com.au</p>
  </main>
</body>
</html>
```